VORLAND COMPOSITES INC website in USA

VORLAND COMPOSITES INC incorporated and operated in USA needs a completely new design of website. This Wyoming based company is a importer and distributor of composites material to supply mainly to American and Canadian/Mexican customers. Our main products includes Carbon Fiber, Aramid Fiber, Glass Fiber, Basalt Fiber, High Silica Glass, Quartz Fiber, S-Glass, Alumina Fiber, Vacuum Auxiliary.

We are one stop composites solution provider for Automotive, Aerospace, Construction, Electrical and Machinery industries.

We are exclusive sales company in North America for BLORAN composites produced from China and their other Asia facilities.

Target Market(s)

USA and Canada

Industry/Entity Type

Composites materials

Coding

Coded - Design and coding required

Number of Pages Required

5+ page

Requirements
Nice to have
• Color theme to match our corporate logo VORLAND. VORLAND stands for Northgate Provisioning Trade Holdings

```html
<!DOCTYPE html>
<html lang="en">
<head>
<meta charset="utf-8">
<title>VORLAND COMPOSITES INC</title>
<link href="https://fonts.googleapis.com/css2?family=Archivo:wght@700;800&family=Roboto+Condensed:wght@400;500;700&display=swap" rel="stylesheet">
<style>
:root{
  --stage:#58585a;
  --green:#5c9e3c;
  --green-dark:#1f4d25;
  --green-mid:#3f7f34;
  --lime:#c9e22a;
  --ink:#111;
  --text:#333;
  --muted:#555;
  --line:#cfcfd4;
  --paper:#f4f4f6;
  --band:#e8e8eb;
  --black:#050505;
}
*{box-sizing:border-box;margin:0;padding:0}
html,body{width:1200px;height:1200px;overflow:hidden}
body{background:var(--stage);font-family:"Roboto Condensed",Arial,sans-serif;color:var(--text);position:relative}
.col{position:absolute;width:378px;overflow:hidden}
.col-left{left:180px;top:0;height:1200px;background:var(--paper)}
.col-right{left:588px;top:10px;height:922px;background:#fff}
.abs{position:absolute}
.heading{font-family:"Archivo",Arial,sans-serif;font-weight:800;color:var(--ink);text-align:center}
.heading-rule::after{content:"";display:block;width:16px;height:1.5px;background:var(--green);margin:3px auto 0}
.center{text-align:center;left:0;right:0}
.small{font-size:5px;line-height:1.45}
.pill{display:inline-flex;align-items:center;gap:3px;border-radius:8px;font-size:4.4px;padding:0 7px;height:11px;border:0.6px solid #333;background:#fff;color:#111}

/* hero */
.hero{left:0;top:0;width:378px;height:290px;background:radial-gradient(ellipse at 60% 40%,#4a4a4a,#1c1c1c 65%,#0b0b0b)}
.hero-head{left:0;top:0;width:378px;height:90px;background:linear-gradient(90deg,#6aa743,#3f8a39 55%,#215a2a);border-radius:0 0 20px 20px}
.brand{left:0;right:0;top:14px;display:flex;justify-content:center;align-items:center;gap:4px}
.brand-mark{width:10px;height:10px;background:var(--lime)}
.brand-name{font-family:"Archivo",Arial,sans-serif;font-weight:800;color:#fff;font-size:14px;letter-spacing:.5px}
.nav{left:21px;top:52px;width:334px;height:23px;border-radius:12px;background:linear-gradient(90deg,#8cc24e,#5da43d 60%,#3c8736);display:flex;align-items:center;justify-content:space-around;padding:0 10px}
.nav a{color:#fff;font-size:8.5px;font-weight:500;text-decoration:none}
.nav a.active{color:var(--lime);border-bottom:1px solid var(--lime)}
.hero-title{top:124px;font-family:"Archivo",Arial,sans-serif;font-weight:800;color:#fff;font-size:13.5px;line-height:17px;text-align:center}
.hero-sub{top:173px;color:#fff;font-size:5.6px;line-height:10px;text-align:center}
.hero-btns{top:235px;display:flex;justify-content:center;gap:10px}
.btn-ghost{height:16px;padding:0 5px;border:0.8px solid #fff;border-radius:3px;color:#fff;font-size:5.4px;display:flex;align-items:center;font-weight:500}
.btn-green{height:16px;padding:0 7px;border-radius:3px;background:#6aa743;color:#fff;font-size:5.4px;display:flex;align-items:center;font-weight:500}
.dots{display:flex;justify-content:center;gap:4px}
.dot{width:5px;height:5px;border-radius:50%;border:0.7px solid #fff}
.dot.on{background:#fff}

/* about */
.about{left:8px;top:317px;width:359px;height:107px;background:#000;display:flex}
.about-photo{width:150px;height:107px;background:linear-gradient(135deg,#dfe3e8,#9aa3ad 55%,#5b6672)}
.about-body{padding:8px 16px;color:#fff}
.about-body h3{font-family:"Archivo",Arial,sans-serif;font-weight:800;font-size:8px;margin-left:4px}
.about-body h3::after{content:"";display:block;width:20px;height:1px;background:#fff;margin-top:2px}
.about-body p{font-size:4.8px;line-height:7.2px;margin-top:12px}
.about-body .pill{margin:10px 0 0 51px;border:none;font-size:4px;height:10px}

/* materials */
.card{position:absolute;width:107px;height:159px;border:0.7px solid var(--line);border-radius:8px;background:#fff;overflow:hidden}
.card h4{font-size:7.3px;font-weight:500;color:#111;text-align:center;margin-top:6px;line-height:9px}
.card p{font-size:4.8px;line-height:7.1px;color:#555;padding:0 7px;margin-top:4px}
.card .apps{color:var(--green)}
.card-photo{position:absolute;left:0;bottom:0;width:107px;height:77px}
.card .pill{position:absolute;left:29px;bottom:10px;border:none;font-size:4px;height:10px}
.explore{top:852px}
.explore .pill{font-size:4px}

/* industries */
.industries{left:0;top:869px;width:378px;height:73px;background:var(--band)}
/* partnership */
.partners{left:0;top:942px;width:378px;height:153px;background:#fff}
.logo-grid{left:58px;top:54px;width:262px;display:grid;grid-template-columns:repeat(9,1fr);row-gap:11px;justify-items:center;align-items:center}
.mark{width:22px;height:6px;border-radius:2px}
.mark.round{width:9px;height:9px;border-radius:50%}

/* downloads */
.downloads{left:0;top:1095px;width:378px;height:105px;background:radial-gradient(ellipse at 80% 40%,#3a3a3a,#141414 60%,#050505)}
.dl-panel{left:61px;top:16px;width:257px;height:75px;border-radius:14px;background:linear-gradient(90deg,#6aa743,#4c8e3b 60%,#2f6b31)}
.dl-folder{left:20px;top:14px;width:42px;height:48px;background:linear-gradient(160deg,#f4f4f4 30%,#f1e633 31%,#e1d21e)}

/* right column */
.rope{left:0;top:0;width:378px;height:254px;background:linear-gradient(135deg,#6ecd63,#49ad49 45%,#7fd56d 70%,#3f9c3f)}
.touch{left:43px;top:127px;width:291px;height:98px;border-radius:10px;background:linear-gradient(90deg,rgba(128,196,64,.92),rgba(90,168,72,.85) 60%,rgba(60,140,70,.75))}
.touch h3{font-family:"Archivo",Arial,sans-serif;font-weight:800;font-size:7.5px;color:#fff;text-align:center;margin-top:26px}
.touch h3::after{content:"";display:block;width:24px;height:1px;background:#fff;margin:3px auto 0}
.touch p{font-size:4.8px;color:#fff;text-align:center;margin-top:7px}
.touch .send{display:block;width:54px;height:16px;margin:15px auto 0;background:#fff;border-radius:3px;font-size:5.2px;font-weight:700;color:#111;text-align:center;line-height:16px}
.reviews{left:0;top:254px;width:378px;height:240px;background:#f6f6f8}
.review{position:absolute;top:97px;width:91px;height:105px;border:0.7px solid #ddd;border-radius:7px;background:#f6f6f8;text-align:center;padding:8px 6px}
.review .who{font-size:5px;line-height:7px;color:#111}
.review .quote{font-size:5px;line-height:6.8px;color:#444;margin-top:7px;letter-spacing:.1px}
.review .stars{position:absolute;left:0;right:0;bottom:12px;font-size:10px;color:#f5b400;letter-spacing:3px}
.review .stars .off{color:#bbb}
.chev{position:absolute;top:148px}
.news{left:0;top:494px;width:378px;height:118px;background:var(--band)}
.email{left:114px;top:73px;width:96px;height:16px;border:0.7px solid #ccc;border-radius:3px;background:#fff;font-size:5px;color:#aaa;text-align:center;line-height:15px}
.subscribe{left:226px;top:73px;width:38px;height:16px;border-radius:3px;background:#000;color:#fff;font-size:5.4px;text-align:center;line-height:16px}
.footer{left:0;top:612px;width:378px;height:310px;background:var(--black);color:#aaa}
.footer-brand{left:0;right:0;top:36px;display:flex;justify-content:center;align-items:center;gap:8px}
.footer-brand .sq{width:34px;height:34px;background:#3d3d3d}
.footer-brand span{font-family:"Archivo",Arial,sans-serif;font-weight:800;font-size:38px;color:#4a4a4a}
.footer .rule{left:22px;width:332px;height:0.6px;background:#444}
.fcol{position:absolute;top:147px;font-size:4.8px;line-height:9.1px;color:#aaa}
.fcol h5{font-size:5.6px;font-weight:500;color:#ddd;margin-bottom:3px}
.fcol .here{color:var(--green)}
.totop{left:347px;top:10px;width:15px;height:15px;border:0.7px solid #888;border-radius:50%;color:#aaa;font-size:6px;text-align:center;line-height:14px}
</style>
</head>
<body>

<main class="col col-left">
  <section class="abs hero" role="img" aria-label="Close-up photograph of dark braided composite fiber rope">
  </section>
  <header class="abs hero-head">
    <div class="abs brand"><span class="brand-mark"></span><span class="brand-name">Bloran</span></div>
    <nav class="abs nav">
      <a class="active">Home</a><a>Products ▾</a><a>Industries</a><a>About Us</a><a>Resources</a><a>Contact</a>
    </nav>
  </header>
  <h1 class="abs center hero-title">Advanced Composite Materials<br>for North American Industries</h1>
  <p class="abs center hero-sub">Exclusive North American distributor of BLORAN COMPOSITES<br>delivering premium carbon, aramid, glass, and specialty fibers for high-performance applications.</p>
  <div class="abs center hero-btns"><span class="btn-ghost">Explore Products</span><span class="btn-green">Request a Quote</span></div>
  <div class="abs center dots" style="top:273px"><span class="dot"></span><span class="dot on"></span><span class="dot"></span></div>

  <section class="abs about">
    <div class="about-photo" role="img" aria-label="Photograph of automated industrial machinery with metal parts"></div>
    <div class="about-body">
      <h3>About VORLAND</h3>
      <p>VORLAND COMPOSITES INC is a Wyoming-based importer and distributor of advanced composite materials. We supply premium fibers and technical fabrics across the United States, Canada, and Mexico.<br>Our partnership with BLORAN COMPOSITES ensures reliable access to world-class materials manufactured in Asia and tailored for the North</p>
      <span class="pill">Learn More About Us →</span>
    </div>
  </section>

  <h2 class="abs center heading heading-rule" style="top:444px;font-size:8px">Our Key Materials</h2>
  <p class="abs center small" style="top:466px;padding:0 44px;line-height:7.3px">VORLAND COMPOSITES provides a comprehensive range of advanced fibers and technical fabrics designed to meet the demands of high-performance industries. From lightweight strength to extreme thermal resistance, our materials enable innovation in automotive, aerospace, and beyond.</p>

  <article class="card" style="left:13px;top:507px">
    <h4>Carbon Fiber</h4>
    <p>Exceptional strength-to-weight ratio and stiffness make carbon fiber the preferred material for structural and performance applications.</p>
    <p style="margin-top:7px"><span class="apps">Applications:</span> Aerospace panels, automotive parts, sports equipment, tooling.</p>
    <div class="card-photo" role="img" aria-label="Photograph of black woven carbon fiber fabric" style="background:linear-gradient(135deg,#4a4a4a,#161616)"></div>
    <span class="pill">Request a quote ↗</span>
  </article>
  <article class="card" style="left:133px;top:507px">
    <h4>Aramid Fiber</h4>
    <p>High tensile strength and superior impact resistance make aramid fiber ideal for protective and reinforcement applications.</p>
    <p style="margin-top:7px"><span class="apps">Applications:</span> Bullet-resistant composites, hoses, insulation, and mechanical protection.</p>
    <div class="card-photo" role="img" aria-label="Photograph of golden yellow aramid fabric" style="background:linear-gradient(135deg,#f5cf3a,#d49a10 60%,#b07808)"></div>
    <span class="pill">Request a quote ↗</span>
  </article>
  <article class="card" style="left:253px;top:507px">
    <h4>Glass &amp; S-Glass Fiber</h4>
    <p>Reliable, cost-effective, and versatile reinforcement fiber with excellent insulation and chemical resistance.</p>
    <p style="margin-top:7px"><span class="apps">Applications:</span> Electrical insulation, laminates, and general-purpose composite structures.</p>
    <div class="card-photo" role="img" aria-label="Photograph of glass fiber yarn spools in white and yellow" style="background:linear-gradient(135deg,#dfeef6,#f1edc8 50%,#ecd94a)"></div>
    <span class="pill">Request a quote ↗</span>
  </article>

  <article class="card" style="left:13px;top:679px">
    <h4>Basalt Fiber</h4>
    <p>Derived from volcanic rock, basalt fiber combines eco-friendliness with superior heat and chemical resistance.</p>
    <p style="margin-top:7px"><span class="apps">Applications:</span> Construction reinforcement, thermal barriers, and high-temperature insulation.</p>
    <div class="card-photo" role="img" aria-label="Photograph of glowing orange basalt fibers" style="background:linear-gradient(135deg,#f7a31f,#e8580e 55%,#f0841c)"></div>
    <span class="pill">Request a quote ↗</span>
  </article>
  <article class="card" style="left:133px;top:679px">
    <h4>Quartz &amp; High Silica Glass</h4>
    <p>High-temperature stability and electrical insulation make quartz and high silica glass fibers essential for extreme environments.</p>
    <p style="margin-top:7px"><span class="apps">Applications:</span> Furnace linings, aerospace heat shields, and electronic insulation.</p>
    <div class="card-photo" role="img" aria-label="Photograph of soft white silica fiber material" style="background:linear-gradient(135deg,#e9e2dc,#f3ece6 50%,#d8c8b8)"></div>
    <span class="pill">Request a quote ↗</span>
  </article>
  <article class="card" style="left:253px;top:679px">
    <h4>Alumina Fiber &amp;Vacuum Auxiliary</h4>
    <p>Specialty materials and process aids supporting precision vacuum infusion and composite molding.</p>
    <p style="margin-top:7px"><span class="apps">Applications:</span> Ceramic insulation, filtration, vacuum bagging consumables.</p>
    <div class="card-photo" role="img" aria-label="Photograph of shimmering blue alumina fiber" style="background:linear-gradient(135deg,#2e3d70,#8fa0c8 50%,#34406a)"></div>
    <span class="pill">Request a quote ↗</span>
  </article>

  <div class="abs center explore" style="text-align:center"><span class="pill">Explore More products →</span></div>

  <section class="abs industries">
    <h2 class="abs center heading heading-rule" style="top:12px;font-size:8px">Industries Served</h2>
    <p class="abs center small" style="top:34px;text-align:center">From electric vehicles to aerospace composites, VORLAND provides tailored materials for each sector.</p>
    <div class="abs" style="left:238px;top:53px"><span class="pill" style="font-size:4px">Learn More →</span></div>
  </section>

  <section class="abs partners">
    <h2 class="abs center heading heading-rule" style="top:8px;font-size:8px">BLORAN Partnership</h2>
    <p class="abs center small" style="top:28px;text-align:center;padding:0 66px;line-height:7.3px">As the exclusive North American sales company for BLORAN COMPOSITES, VORLAND delivers proven material technologies directly from Asian production facilities with local support, quality assurance, and fast shipping.</p>
    <div class="abs logo-grid" aria-label="Partner and client badges">
      <span class="mark" style="background:#2b6cc4"></span><span class="mark" style="background:#d83a2e"></span><span class="mark" style="background:#2a7fd0"></span><span class="mark" style="background:#1a4aa0"></span><span class="mark" style="background:#555"></span><span class="mark" style="background:#3aa0a0"></span><span class="mark round" style="background:#c9202f"></span><span class="mark" style="background:#1b3c8c"></span><span class="mark" style="opacity:0"></span>
      <span class="mark" style="background:#1f4fa3"></span><span class="mark" style="background:#1d8f6a"></span><span class="mark" style="background:#d4223a"></span><span class="mark" style="background:#3c78c8"></span><span class="mark" style="background:#999"></span><span class="mark" style="background:#c3363a"></span><span class="mark round" style="background:#1c9a4a"></span><span class="mark round" style="background:#d6b21a"></span><span class="mark" style="opacity:0"></span>
      <span class="mark" style="background:#3d78c0"></span><span class="mark" style="background:#d46060"></span><span class="mark" style="background:#d41e26"></span><span class="mark" style="background:#2c3e8e"></span><span class="mark round" style="background:#e04a2a"></span><span class="mark round" style="background:#c73030"></span><span class="mark round" style="background:#b8283a"></span><span class="mark" style="background:#e6a01c"></span><span class="mark" style="opacity:0"></span>
    </div>
    <div class="abs" style="left:157px;top:131px"><span class="pill" style="font-size:4px">Discover BLORAN Partnership →</span></div>
  </section>

  <section class="abs downloads">
    <svg class="abs" width="378" height="105" aria-hidden="true" style="left:0;top:0">
      <line x1="0" y1="100" x2="170" y2="0" stroke="#8bc34a" stroke-width="0.8"/>
      <line x1="205" y1="0" x2="378" y2="90" stroke="#d7e32a" stroke-width="0.8"/>
      <line x1="275" y1="105" x2="378" y2="40" stroke="#cfcfcf" stroke-width="0.6"/>
    </svg>
    <div class="abs dl-panel">
      <div class="abs dl-folder" role="img" aria-label="Illustration of a yellow folder holding documents"></div>
      <h3 class="abs heading" style="left:84px;top:17px;font-size:8px;color:#fff">Technical Downloads</h3>
      <p class="abs" style="left:85px;top:42px;font-size:5px;line-height:7.2px;color:#fff;text-align:center">Find product datasheets, specifications,<br>and material safety documents in one place.</p>
      <span class="abs pill" style="left:187px;top:33px;border:none;font-size:4px">Download Resources</span>
    </div>
  </section>
</main>

<aside class="col col-right">
  <section class="abs rope" role="img" aria-label="Photograph of twisted green fiber rope"></section>
  <div class="abs touch">
    <h3>Get in touch</h3>
    <p>Need technical guidance or a quotation? Our specialists are ready to assist.</p>
    <span class="send">Send Request</span>
  </div>

  <section class="abs reviews">
    <h2 class="abs center heading heading-rule" style="top:26px;font-size:8px">What Our Clients Say</h2>
    <p class="abs center small" style="top:52px;text-align:center;padding:0 40px;line-height:7.3px">Our clients across North America trust VORLAND COMPOSITES for consistent quality, reliable delivery, and technical expertise. Here's what some of them have to say.</p>
    <svg class="chev" style="left:16px" width="10" height="18" aria-hidden="true"><polyline points="8,1 1,9 8,17" fill="none" stroke="#555" stroke-width="0.8"/></svg>
    <svg class="chev" style="left:351px" width="10" height="18" aria-hidden="true"><polyline points="2,1 9,9 2,17" fill="none" stroke="#555" stroke-width="0.8"/></svg>
    <div class="review" style="left:42px">
      <div class="who">Marcus D., Senior Engineer<br>Skyvane Structures</div>
      <div class="quote">“VORLAND's materials have consistently met our technical requirements. Their support team understands our production needs and responds fast.”</div>
      <div class="stars">★★★★<span class="off">☆</span></div>
    </div>
    <div class="review" style="left:142px">
      <div class="who">Helen P., Procurement Manager<br>Ampline Motors</div>
      <div class="quote">“We've worked with many suppliers, but VORLAND stands out for their reliability and transparent communication. Deliveries are always on schedule.”</div>
      <div class="stars">★★★★<span class="off">☆</span></div>
    </div>
    <div class="review" style="left:242px">
      <div class="who">Rafael O., Materials Lab Director<br>Buildora Labs</div>
      <div class="quote">“Excellent quality and documentation. The data sheets were clear, and the fibers performed exactly as specified in testing.”</div>
      <div class="stars">★★★★<span class="off">☆</span></div>
    </div>
    <div class="abs center dots" style="top:223px"><span class="dot" style="border-color:#888"></span><span class="dot" style="border-color:#888"></span><span class="dot" style="border-color:#888"></span><span class="dot" style="background:#888;border-color:#888"></span><span class="dot" style="border-color:#888"></span></div>
  </section>

  <section class="abs news">
    <h2 class="abs center heading heading-rule" style="top:28px;font-size:8px">Join Our Community of Innovators.</h2>
    <p class="abs center small" style="top:48px;text-align:center">Receive exclusive news, technical articles, and updates about our composite solutions—helping you design lighter, stronger, and smarter.</p>
    <div class="abs email">Your Email</div>
    <div class="abs subscribe">Suscribe</div>
  </section>

  <footer class="abs footer">
    <div class="abs totop">↑</div>
    <div class="abs footer-brand"><span class="sq"></span><span>Bloran</span></div>
    <p class="abs center" style="top:99px;font-size:4.6px;line-height:6.8px;text-align:center;color:#bbb">VORLAND COMPOSITES INC<br>Exclusive North American sales company for BLORAN COMPOSITES.<br>Supplying advanced fibers and composite materials for Automotive, Aerospace, Construction, Electrical, and Machinery industries.</p>
    <div class="abs rule" style="top:131px"></div>
    <div class="fcol" style="left:22px"><h5>Quick Links</h5><span class="here">Home ↗</span><br>About Us ↗<br>Products ↗<br>Industries ↗<br>Resources ↗<br>Contact ↗<br>Request a Quote ↗<br>Downloads ↗</div>
    <div class="fcol" style="left:89px"><h5>Products</h5>Carbon Fiber ↗<br>Aramid Fiber ↗<br>Glass &amp; S-Glass ↗<br>Basalt Fiber ↗<br>High Silica Glass ↗<br>Quartz Fiber ↗<br>Alumina Fiber ↗<br>Vacuum Auxiliary ↗</div>
    <div class="fcol" style="left:171px;line-height:9.1px"><h5>Resources</h5>Technical Data ↗<br><span style="position:relative;top:-2px">Sheets ↗</span><br>Certifications ↗<br>Case Studies ↗<br>News &amp; Blog ↗<br>Privacy Policy ↗<br>Terms of Use ↗</div>
    <div class="fcol" style="left:241px;line-height:7px"><h5 style="margin-bottom:5px">Contact</h5>Head Office:<br>480 Prairie Ridge Road, Laramie, Wyoming, USA<br><br>sales@vorlandcomposites.com<br><br>+1 (555) 018-2290<br><br>Office Hours: Monday – Friday, 9:00 AM – 6:00 PM (MST)</div>
    <div class="abs rule" style="top:253px"></div>
    <p class="abs center" style="top:264px;font-size:4px;text-align:center;color:#999">© 2025 VORLAND COMPOSITES INC. All rights reserved. Exclusive North American Partner of BLORAN COMPOSITES.</p>
    <p class="abs center" style="top:282px;font-size:4px;text-align:center;color:#999;word-spacing:1px">Privacy Policy &nbsp;&nbsp;&nbsp;&nbsp;&nbsp;&nbsp;&nbsp; Terms of Use &nbsp;&nbsp;&nbsp;&nbsp;&nbsp;&nbsp;&nbsp; Site Map</p>
  </footer>
</aside>

</body>
</html>
```